Label for kQm Ranch beef tallow

I need a small label to go on a 2oz amber glass jar as well as a 4 oz. amber glass jar of moisturizer.
I prefer it to be rectangular for the 2oz jar since it's small and square for the 4oz jar.
I'd like to keep our kQm Ranch logo the same font and style, which is attached. Ten Sleep, Wyoming should be left out. The font for kQm Ranch is spartan.
The label content is as follows:
Signature Tallow
Whipped Moisturizer
Ingredients: Beef Tallow, jojoba oil, peppermint oil.
2oz. jar

Instead of a white label, I'm thinking of a tan or brown label that will blend in with the amber jar. The lettering could then be a white, cream or even rust/burgandy color. Something to give it a rich look.

Thank you!

Target Market(s)

Mainly women but men as well.

Industry/Entity Type

Ranching and online beef sales

Requirements
Must have
• kQm Ranch logo

```html
<!DOCTYPE html>
<html lang="en">
<head>
<meta charset="utf-8">
<title>kQm Ranch – Signature Tallow Labels</title>
<link rel="stylesheet" href="https://fonts.googleapis.com/css2?family=League+Spartan:wght@400;700;800&display=swap">
<style>
  :root {
    --backdrop: #d3b48c;
    --label-burgundy: #5e2631;
    --label-cream: #d5b68f;
  }
  * { margin: 0; padding: 0; box-sizing: border-box; }
  html, body {
    width: 1200px;
    height: 750px;
    overflow: hidden;
    background: var(--backdrop);
  }
  .canvas {
    position: relative;
    width: 1200px;
    height: 750px;
    font-family: "League Spartan", sans-serif;
  }
  .label {
    position: absolute;
    display: block;
  }
  .label--small { left: 248px; top: 337px; width: 308px; height: 198px; }
  .label--large { left: 687px; top: 250px; width: 266px; height: 283px; }
  .label .panel { fill: var(--label-burgundy); }
  .label .trim { fill: var(--label-cream); }
  .label .arc-text {
    fill: var(--label-cream);
    font-family: "League Spartan", sans-serif;
    font-weight: 800;
    letter-spacing: 1px;
  }
  .label .brand-name {
    fill: var(--label-cream);
    font-family: "League Spartan", sans-serif;
    font-weight: 400;
  }
  .label .ingredients,
  .label .net-weight {
    fill: var(--label-cream);
    font-family: "League Spartan", sans-serif;
    font-weight: 700;
  }
</style>
</head>
<body>
<main class="canvas">

  <!-- 2 oz rectangular label -->
  <svg class="label label--small" viewBox="0 0 308 198" aria-label="kQm Ranch Signature Tallow 2 oz label">
    <rect class="panel" x="0" y="0" width="308" height="198"/>
    <rect class="trim" x="0" y="0" width="308" height="6"/>
    <rect class="trim" x="0" y="190" width="308" height="6"/>
    <defs>
      <path id="small-top-arc" d="M 94 101 A 64 64 0 0 1 222 101"/>
      <path id="small-bottom-arc" d="M 84 101 A 74 74 0 0 0 232 101"/>
    </defs>
    <text class="arc-text" font-size="14">
      <textPath href="#small-top-arc" startOffset="50%" text-anchor="middle">SIGNATURE TALLOW</textPath>
    </text>
    <text class="arc-text" font-size="14">
      <textPath href="#small-bottom-arc" startOffset="50%" text-anchor="middle">WHIPPED MOISTURIZER</textPath>
    </text>
    <text class="brand-name" x="158" y="102" font-size="30" text-anchor="middle">kQm</text>
    <text class="brand-name" x="158" y="126" font-size="20" text-anchor="middle">RANCH</text>
    <text class="ingredients" font-size="8.5" transform="translate(16 178) rotate(-90)">
      <tspan x="0" y="0">BEEF TALLOW, JOJOBA OIL</tspan>
      <tspan x="0" y="10">PEPPERMINT OIL.</tspan>
    </text>
    <text class="net-weight" x="300" y="178" font-size="11" text-anchor="end">2OZ.</text>
  </svg>

  <!-- 4 oz square label -->
  <svg class="label label--large" viewBox="0 0 266 283" aria-label="kQm Ranch Signature Tallow 4 oz label">
    <rect class="panel" x="0" y="0" width="266" height="283"/>
    <rect class="trim" x="0" y="0" width="266" height="7"/>
    <rect class="trim" x="0" y="276" width="266" height="7"/>
    <defs>
      <path id="large-top-arc" d="M 53 130 A 81 81 0 0 1 215 130"/>
      <path id="large-bottom-arc" d="M 41 130 A 93 93 0 0 0 227 130"/>
    </defs>
    <text class="arc-text" font-size="17">
      <textPath href="#large-top-arc" startOffset="50%" text-anchor="middle">SIGNATURE TALLOW</textPath>
    </text>
    <text class="arc-text" font-size="17">
      <textPath href="#large-bottom-arc" startOffset="50%" text-anchor="middle">WHIPPED MOISTURIZER</textPath>
    </text>
    <text class="brand-name" x="134" y="135" font-size="38" text-anchor="middle">kQm</text>
    <text class="brand-name" x="134" y="166" font-size="25" text-anchor="middle">RANCH</text>
    <text class="ingredients" font-size="9.5">
      <tspan x="22" y="254">BEEF TALLOW, JOJOBA OIL</tspan>
      <tspan x="22" y="266">PEPPERMINT OIL.</tspan>
    </text>
    <text class="net-weight" x="246" y="259" font-size="12" text-anchor="end">4OZ.</text>
  </svg>

</main>
</body>
</html>
```